Professional Package for CPA Firm

We would like a stationery design for our new CPA Firm based in Atlanta, GA called 'Vale 8'. We work with investors to help grow investments, tax free. We would like the design to have a professional/minimal look with a 'wow' factor. We need 9.5″ x 4.125″, 9x12, and 10x13 mailing envelopes, business cards, and a letterhead. We have a logo that is already complete. For the letterhead, we would like to have space to put credentials at the bottom of the page

Industry/Entity Type

CPA, Accounting

```html
<!DOCTYPE html>
<html lang="en">
<head>
<meta charset="utf-8">
<title>Vale 8 – Business Card</title>
<link rel="stylesheet" href="https://fonts.googleapis.com/css2?family=Lato:wght@300;400;700&display=swap">
<style>
  :root {
    --backdrop: #1c1d20;
    --navy: #0f3452;
    --coral: #f2555a;
    --teal: #1fb6c4;
    --silver: #c9ccd1;
    --white: #ffffff;
  }
  * { margin: 0; padding: 0; box-sizing: border-box; }
  html, body {
    width: 1200px; height: 874px; overflow: hidden;
    background: var(--backdrop);
    font-family: "Lato", sans-serif;
  }
  .sheet {
    width: 1200px; height: 874px;
    display: flex; align-items: center; justify-content: center; gap: 80px;
  }
  .card {
    width: 380px; height: 640px;
    background: var(--navy);
    border-radius: 18px;
    position: relative;
    overflow: hidden;
  }
  /* Front */
  .card-front {
    display: flex; flex-direction: column; align-items: center; justify-content: center;
  }
  .brand {
    display: flex; align-items: center; gap: 14px;
  }
  .brand-dot {
    width: 18px; height: 18px; border-radius: 50%; background: var(--coral);
  }
  .brand-name {
    font-weight: 700; font-size: 54px; letter-spacing: 2px; color: var(--silver);
  }
  .tagline {
    margin-top: 10px;
    font-weight: 300; font-size: 17px; letter-spacing: 2.5px; color: var(--silver);
  }
  /* Back */
  .card-back { padding: 60px 48px; }
  .back-brand {
    display: flex; align-items: center; gap: 12px;
    font-weight: 700; font-size: 40px; letter-spacing: 1.5px; color: var(--white);
  }
  .back-brand .brand-dot { width: 14px; height: 14px; }
  .person {
    margin-top: 150px;
    width: 230px;
  }
  .person-name {
    font-weight: 400; font-size: 26px; letter-spacing: 0.5px; color: var(--teal);
    padding-bottom: 6px; border-bottom: 1px solid var(--silver);
  }
  .person-role {
    font-size: 15px; color: var(--coral); text-align: right; margin-top: -2px;
    position: relative; top: -24px; display: none;
  }
  .role {
    font-size: 15px; color: var(--coral); margin-top: 6px; text-align: right;
  }
  .contact { margin-top: 56px; list-style: none; }
  .contact li {
    display: flex; align-items: flex-start; gap: 10px;
    font-size: 15px; line-height: 22px; color: var(--white);
  }
  .contact li + li { margin-top: 2px; }
  .contact .gap { margin-top: 14px; }
  .contact svg { width: 14px; height: 14px; margin-top: 4px; flex: none; fill: var(--coral); }
  .contact .text { border-left: 1px solid var(--white); padding-left: 8px; }
</style>
</head>
<body>
<main class="sheet">
  <section class="card card-front" aria-label="Card front">
    <div class="brand">
      <span class="brand-dot"></span>
      <span class="brand-name">Vale 8</span>
    </div>
    <p class="tagline">CPAs and Tax Advisors</p>
  </section>

  <section class="card card-back" aria-label="Card back">
    <div class="back-brand"><span class="brand-dot"></span>Vale 8</div>

    <div class="person">
      <h1 class="person-name">DANIEL REYES</h1>
      <p class="role">President</p>
    </div>

    <ul class="contact">
      <li>
        <svg viewBox="0 0 14 14"><path d="M7 0a5 5 0 0 0-5 5c0 3.5 5 9 5 9s5-5.5 5-9a5 5 0 0 0-5-5zm0 7a2 2 0 1 1 0-4 2 2 0 0 1 0 4z"/></svg>
        <span class="text">214 Linden Court<br>Atlanta, Georgia 30309</span>
      </li>
      <li class="gap">
        <svg viewBox="0 0 14 14"><path d="M3 0l3 3-2 2c1 2 3 4 5 5l2-2 3 3-2 3C6 14 0 8 0 3z"/></svg>
        <span class="text">404-555-0142</span>
      </li>
      <li>
        <svg viewBox="0 0 14 14"><path d="M4 0h6a1 1 0 0 1 1 1v12a1 1 0 0 1-1 1H4a1 1 0 0 1-1-1V1a1 1 0 0 1 1-1zm1 2v8h4V2zm2 9a1 1 0 1 0 0 2 1 1 0 0 0 0-2z"/></svg>
        <span class="text">404-555-0187</span>
      </li>
      <li>
        <svg viewBox="0 0 14 14"><path d="M0 3h14v8H0zm1 1l6 4 6-4v-.5H1z"/></svg>
        <span class="text">info@vale8.com</span>
      </li>
      <li>
        <svg viewBox="0 0 14 14"><path d="M7 0a7 7 0 1 0 0 14A7 7 0 0 0 7 0zm0 1.5c.8 0 1.6 2 1.8 4.5H5.2C5.4 3.5 6.2 1.5 7 1.5zM5.2 7.5h3.6C8.6 10 7.8 12.5 7 12.5S5.4 10 5.2 7.5z"/></svg>
        <span class="text">www.vale8.com</span>
      </li>
    </ul>
  </section>
</main>
</body>
</html>
```